Chatterloom Advertisement for EV chargers

Project Overview:
We are excited to launch a new Chatterloom ad campaign to promote our top-notch service of Electric Vehicle (EV) Charger Installation. This campaign aims to reach environmentally conscious individuals, homeowners, businesses, and EV owners seeking professional and reliable EV charger installation solutions. The primary goal is to increase brand awareness and generate leads for our EV charger installation service.
Target Audience:
Our target audience includes environmentally conscious homeowners, property managers, commercial businesses, and individuals who own or plan to purchase an electric vehicle. The age range for our target audience is between 25 to 65 years old, residing in [your service area location] or nearby regions.
Key Message:
The advertisement should convey the following key messages:
"Power Up Your Ride with Professional EV Charger Installation."
"Fast and Reliable Service for Home and Business EV Charging Solutions."
"Go Green with Clean Energy and Eco-friendly EV Charging."
"Experienced Installers for Hassle-free EV Charger Setups."
Design Requirements:
Dimensions: The advertisement should comply with Chatterloom's recommended ad dimensions (e.g., 1200 x 628 pixels).
Branding: Incorporate our company logo and colors (Logo attached).
Visuals: Use high-quality images or graphics showcasing electric vehicles being charged at home and in commercial settings, highlighting the ease and convenience of the process.
Call-to-Action (CTA): Include a clear and compelling CTA button, such as "Get a Quote," "Book Now," or "Learn More."
Text: Keep the text concise, using persuasive language to emphasize the benefits of our EV charger installation service, such as expert technicians, efficient installations, and cost savings.
Testimonials: Feature positive customer reviews or testimonials (if available) to build trust and credibility.
Coverage Area: Mention your service coverage area to ensure relevancy to the target audience.
Offer: If applicable, consider offering a limited-time discount or promotion for EV charger installation services.
Target Market(s)
Target Audience: Our target audience includes environmentally conscious homeowners, property managers, commercial businesses, and individuals who own or plan to purchase an electric vehicle. The age range for our target audience is between 25 to 65 years old, residing in [your service area location] or nearby regions.
Requirements
Must have
- The advertisement should convey the following key messages: "Power Up Your Ride with Professional EV Charger Installation." "Fast and Reliable Service for Home and Business EV Charging Solutions." "Go Green with Clean Energy and Eco-friendly EV Charging." "Experienced Installers for Hassle-free EV Charger Setups." Design Requirements: Dimensions: The advertisement should comply with Chatterloom's recommended ad dimensions (e.g., 1200 x 628 pixels). Branding: Incorporate our company logo and colors (Logo attached). Visuals: Use high-quality images or graphics showcasing electric vehicles being charged at home and in commercial settings, highlighting the ease and convenience of the process. Call-to-Action (CTA): Include a clear and compelling CTA button, such as "Get a Quote," "Book Now," or "Learn More." Text: Keep the text concise, using persuasive language to emphasize the benefits of our EV charger installation service, such as expert technicians, efficient installations, and cost savings. Testimonials: Feature positive customer reviews or testimonials (if available) to build trust and credibility. Coverage Area: Mention your service coverage area to ensure relevancy to the target audience. Offer: If applicable, consider offering a limited-time discount or promotion for EV charger installation services.

```html
<!DOCTYPE html>
<html lang="en">
<head>
<meta charset="utf-8">
<title>Harlow Energy – EV Charging Solutions</title>
<link href="https://fonts.googleapis.com/css2?family=Poppins:ital,wght@0,300;0,400;0,600;0,700;1,400&display=swap" rel="stylesheet">
<style>
  :root {
    --brand-red: #b3162b;
    --ink-dark: #2a3038;
    --ink-mid: #4a525c;
    --text-light: #ffffff;
  }
  * { margin: 0; padding: 0; box-sizing: border-box; }
  html, body { width: 1200px; height: 628px; overflow: hidden; background: #ffffff; }
  .ad {
    position: relative;
    width: 1200px;
    height: 628px;
    overflow: hidden;
    font-family: "Poppins", sans-serif;
    color: var(--text-light);
  }
  .backdrop {
    position: absolute;
    inset: 0;
    background:
      radial-gradient(ellipse at 15% 20%, rgba(110,118,128,0.55), transparent 60%),
      linear-gradient(100deg, var(--ink-mid) 0%, var(--ink-dark) 45%, #3a4049 70%);
  }
  .scene {
    position: absolute;
    inset: 0;
    width: 1200px;
    height: 628px;
  }
  .brand-name {
    position: absolute;
    left: 52px;
    top: 52px;
    font-weight: 600;
    font-size: 24px;
    line-height: 1;
    letter-spacing: 0.5px;
    color: var(--text-light);
  }
  .accent-bar {
    position: absolute;
    left: 0;
    top: 186px;
    width: 18px;
    height: 120px;
    background: var(--brand-red);
  }
  .headline {
    position: absolute;
    left: 52px;
    top: 194px;
    font-size: inherit;
    font-weight: inherit;
  }
  .headline-lead {
    display: block;
    font-weight: 300;
    font-size: 26px;
    line-height: 29px;
  }
  .headline-main {
    display: block;
    font-weight: 600;
    font-size: 41.5px;
    line-height: 50px;
    letter-spacing: 0.2px;
    margin-top: 2px;
  }
  .intro {
    position: absolute;
    left: 52px;
    top: 357px;
    width: 520px;
    font-style: italic;
    font-size: 15px;
    line-height: 19px;
  }
  .cta {
    position: absolute;
    left: 148px;
    top: 502px;
    width: 310px;
    height: 55px;
    border-radius: 10px;
    background: var(--brand-red);
    display: flex;
    align-items: center;
    justify-content: center;
    font-weight: 600;
    font-size: 27px;
    letter-spacing: 0.3px;
    color: var(--text-light);
    text-decoration: none;
  }
</style>
</head>
<body>
<main class="ad">
  <div class="backdrop" role="img" aria-label="Dimmed photo of an electric car plugged into a charging station"></div>

  <svg class="scene" viewBox="0 0 1200 628">
    <defs>
      <linearGradient id="photoTone" x1="0" y1="0" x2="1" y2="1">
        <stop offset="0" stop-color="#d3d7db"/>
        <stop offset="0.45" stop-color="#9aa1a8"/>
        <stop offset="0.8" stop-color="#3b4149"/>
        <stop offset="1" stop-color="#1e2329"/>
      </linearGradient>
    </defs>
    <path class="curve-band" d="M648 0 C570 180 586 440 928 628 L1200 628 L1200 0 Z" fill="var(--brand-red)"/>
    <path class="curve-photo" role="img" aria-label="Photo of a man in a dark jacket plugging a charging cable into a white electric car in front of an office building"
          d="M668 0 C596 180 616 430 962 628 L1200 628 L1200 0 Z" fill="url(#photoTone)"/>
  </svg>

  <div class="brand-name">HARLOW ENERGY</div>

  <div class="accent-bar"></div>

  <h1 class="headline">
    <span class="headline-lead">Fast and Reliable Service</span>
    <span class="headline-lead">for Home and Business</span>
    <span class="headline-main">EV CHARGING SOLUTIONS</span>
  </h1>

  <p class="intro">We understand that every business or home has different energy requirements. This is why we implement a collaborative approach and customise a package to align with your energy goals.</p>

  <a class="cta" href="#quote">GET A QUOTE</a>
</main>
</body>
</html>
```